Systems and Technology Consultants - Website

Design & Build a website for a new company which operates in the Systems and Technology space for Transportation, Government and Commercial sectors.

Overall design should be minimalist in nature.
Should also have a feed that provides news and event updates on the main page.
Logo has already been awarded and should be incorporated into the site.

We like the overall layout, functionality and simplicity of the below sites. Submitted designs could be similar to or a combination of the aspects on these sites, or perhaps a whole different concept - we are open to new ideas.
Norvique.com
Teblo.it

Update 1 Dated 27 May 2014

All I am moving away from the Teblo.it website and would like it to be more aligned with Norvique.com not only in layout but in functionality. I will be extending the deadline of this design brief for two weeks to incorporate additional requirements and will add addtional funding to the project.

Apologies for not having more information available to provide but with so many submissions its getting confusing.

Thanks Derek

Please note that the brief has been updated and the deadline has been extended.

Important: We will need two language versions of the website, English and Arabic; the website is hosted on HostPelican

Hello All, Thank you for your submissions. We have narrowed it down to the final 6 designers and I just wanted to take a moment and provide a bit of feedback regarding the concepts that we like and the modifications we are looking for. First, let me mention some of the design functions we like. - At the top of the homepage we really like the "region" or "language" tab so that the website can be viewed in both English and Arabic. - We like the homepage to have clear color variation so that the different sections of the homepage are distinct. Additionally, we like the bottom portion of the homepage to be in red. We feel that draws attention to our contact information. Again, we would like the colors to integrate black, gray-scale, red, etc. - Having a search tab at the top of the home page, or integrated into the main image, so that the site is easy to navigate. - We especially like the main image to have the scrolling tabs at the bottom so it is easy to browse the services offered (Consultancy, Solutions Architecture, Masters Systems Integration, Independent Design Review). - In regards to the services offered tab we really like the idea that a few people presented that have the outside of our logo with an icon in the middle of consultancy, solutions, etc., etc. Secondly, as mentioned in our brief we really enjoy the design of norvique site. Specially, we enjoy the strong iconic images they use, the way the tabs at the top scroll easily, and contact us page that generates an email. Lastly, I've included some photos of the concept we have been working on. What we are trying to demonstrate is how our company offers a range of services that are essentially linked together. We provide individual services that when combined present the full service package. We would like this concept to be integrated into the over concept of our website. Please feel free to ask for clarification of any of the above points or contact us if you have any additional questions. We appreciate all of your hard work and are very excited to see the updated designs. Best, Marta Vennick Quelbrant Senior Program Manager marta.vennick@quelbrant-example.com

Industry/Entity Type

Government

Font styles to use
Serif
Sans Serif

Requirements
Must have
• Must work on/adapt to various/mobile devices (responsive)
Must be simple and straightforward
Colors should be in line/matching with logo
2 language versions: English and Arabic (no Thai)
Services should be the first group/row of items after/below the main image
Note: the website will be hosted by hostpelican
Nice to have
• Submit feedback form
What's New section
The banner at the bottom of the site should not be too large; we would like a narrow one more
It would be nice if the header/top banner (with Home, About, etc. tabs) could stay in place as you scroll down (like Norvique and Chatterloop)
We will likely only use one image with a Company slogan on the Home page rather than a carousel of images to rotate through
Should not have
• This is the existing website: http://www.quelbrant-example.org
We do not like the animation, the way the banner icons/titles bounce
Not simple enough, we don't like the functionality or how pages load so slowly
We do not like the logo centered - it should be at the left
The banner and its tabs should not be towards the right, we would like them to be centered, to go all the way across and to be below the logo

```html
<!DOCTYPE html>
<html lang="en">
<head>
<meta charset="utf-8">
<title>Quelbrant International</title>
<link rel="stylesheet" href="https://fonts.googleapis.com/css2?family=Open+Sans:wght@400;600;700&display=swap">
<style>
:root{
  --red:#e8222a;
  --ink:#333;
  --muted:#777;
  --line:#ddd;
  --pink:rgba(240,110,120,.85);
  --purple:#b097c9;
  --sky:#7ecbea;
  --rose:#e07f8a;
  --mint:#8fcf98;
  --steel:#8aa8d2;
  --footer:#3b3b47;
  --footer-dark:#2c2c36;
}
*{box-sizing:border-box;margin:0;padding:0}
html,body{width:847px;height:1200px;overflow:hidden;background:#fff}
body{position:relative;font-family:"Open Sans",Arial,sans-serif;color:var(--ink)}
.abs{position:absolute}
/* header */
.header{left:0;top:0;width:847px;height:77px;border-top:1px solid var(--red);background:#fff}
.brand{left:68px;top:18px;display:flex;align-items:center;gap:6px;color:var(--red);font-weight:700;font-size:15px;letter-spacing:1.5px}
.brand-mark{width:12px;height:12px;background:var(--red)}
.lang{left:571px;top:19px;font-size:8px;color:var(--muted);display:flex;gap:5px;align-items:center}
.flag{width:10px;height:7px;background:linear-gradient(#b22 0 50%,#fff 50%);border:1px solid #bbb}
.search{left:653px;top:16px;width:123px;height:17px;background:#e8e8e8}
.search-btn{right:0;top:0;width:17px;height:17px;background:var(--red)}
.nav{left:337px;top:49px;display:flex;gap:0;font-size:9.5px;color:#555}
.nav a{display:block;padding:2px 8px;margin-right:19px;color:inherit;text-decoration:none}
.nav a.active{background:var(--red);color:#fff;font-weight:600}
/* hero */
.hero{left:0;top:77px;width:847px;height:351px;background:linear-gradient(100deg,#d9dde3 0%,#c7ced8 35%,#a4adba 60%,#cfd4db 100%)}
.arrow{width:28px;height:28px;border-radius:50%;border:1.5px solid}
.promo{left:541px;top:143px;width:183px;height:217px;background:var(--pink);text-align:center;color:#222}
.promo-name{margin-top:20px;font-weight:700;font-size:19px;letter-spacing:4px}
.promo-sub{font-size:8px;letter-spacing:6px;font-weight:600}
.promo-title{margin:17px 12px 0;font-size:10px;line-height:1.45}
.promo-text{margin:10px 12px 0;font-size:8px;line-height:1.3;color:#fff;font-weight:600}
.btn-dark{display:inline-block;margin-top:24px;background:#1e1e1e;color:#fff;font-size:8.5px;padding:7px 16px;font-weight:600}
/* services */
.tile{top:455px;width:126px;height:71px;color:#fff;font-size:12.5px;font-weight:600;text-align:center;padding-top:12px}
.tile svg{display:block;margin:0 auto 3px}
/* sections */
.sec-head{display:flex;align-items:center;gap:8px;color:var(--red);font-size:13px;font-weight:600}
.sec-mark{width:10px;height:10px;border:2px solid var(--red)}
.rule{height:1px;background:var(--line)}
.rule-red{height:1px;background:var(--red)}
.about-text{left:178px;top:600px;width:187px;font-size:8.4px;line-height:1.27;color:#555;text-align:justify}
.news-meta{left:592px;top:603px;font-size:6.5px;color:#333;font-weight:600}
.news-title{left:616px;top:617px;width:160px;font-size:10px;font-weight:700;line-height:1.45}
.stars{color:#333;font-size:10px;letter-spacing:1px}
.news-text{left:593px;top:671px;width:170px;font-size:6.7px;line-height:1.35;color:#444}
.btn-red{background:var(--red);color:#fff;font-size:7px;font-weight:600;padding:4px 6px}
.card{top:799px;width:155px;height:145px;border:1px solid #eee;border-top:none}
.card-img{height:70px}
.card h3{font-size:9.7px;font-weight:400;margin:11px 0 0 1px;color:#222}
.card p{font-size:7.8px;color:#999;margin:11px 0 0 1px}
.card p span{color:var(--red)}
.card .rate{margin:3px 0 0 1px;font-size:9px;letter-spacing:-1px;color:#ccc}
.card .rate b{color:#f2c21b;font-weight:400}
/* footer */
.footer{left:0;top:989px;width:847px;height:169px;background:var(--footer);color:#fff}
.foot-title{left:0;width:847px;top:45px;text-align:center;font-size:11.5px;font-weight:600}
.foot-mark{left:420px;top:14px;width:10px;height:10px;border:2px solid #fff}
.branch{top:72px;width:170px;font-size:6.4px;line-height:1.35;color:#ddd}
.branch h4{font-size:10px;font-weight:600;color:#eee;margin-bottom:1px}
.branch dl{margin-top:7px;display:grid;grid-template-columns:28px 1fr;row-gap:3px}
.branch dt{color:#6f8fc7}
.contact h4{font-size:8px;font-weight:600;text-align:center;color:#fff}
.field{width:108px;height:18px;margin-top:7px;background:#2e2e38;border:1px solid #4a4a56;color:#aaa;font-size:7px;text-align:center;line-height:16px}
.btn-contact{width:108px;height:18px;margin-top:12px;background:var(--red);color:#fff;font-size:8px;text-align:center;line-height:18px;font-weight:600}
.bottom{left:0;top:1158px;width:847px;height:42px;background:var(--footer-dark);color:#eee;font-size:7.5px}
.social{right:70px;top:15px;display:flex;gap:9px}
.social span{width:11px;height:11px;background:#e8e8ec;border-radius:2px}
</style>
</head>
<body>

<header class="abs header">
  <div class="abs brand"><span class="brand-mark"></span>QUELBRANT</div>
  <div class="abs lang">Language: <span class="flag"></span> ▾</div>
  <div class="abs search"><div class="abs search-btn">
    <svg width="17" height="17" viewBox="0 0 17 17"><circle cx="7.5" cy="7.5" r="3" fill="none" stroke="#fff" stroke-width="1.3"/><line x1="9.7" y1="9.7" x2="12" y2="12" stroke="#fff" stroke-width="1.3"/></svg>
  </div></div>
  <nav class="abs nav">
    <a class="active">Home</a><a>Business Units</a><a>Service</a><a>About Us</a><a>Locations</a><a>Contact Us</a>
  </nav>
</header>

<section class="abs hero" role="img" aria-label="Photo of a presenter addressing business people in a bright meeting room"></section>
<div class="abs arrow" style="left:29px;top:237px;border-color:rgba(255,255,255,.7)"></div>
<div class="abs arrow" style="left:789px;top:237px;border-color:var(--red)">
  <svg width="25" height="25" viewBox="0 0 25 25"><path d="M11 8l4.5 4.5L11 17" fill="none" stroke="#e8222a" stroke-width="1.4"/></svg>
</div>
<div class="abs promo">
  <div class="promo-name">QUELBRANT</div>
  <div class="promo-sub">TECHNIK</div>
  <div class="promo-title">Systems and Technology space for Transportation</div>
  <div class="promo-text">Lorem ipsum dolor sit amet, consectetur adipiscing elit. Maecenas ursus tristique convallis. Class aptent taciti sociosqu ad litora</div>
  <div class="btn-dark">READ MORE</div>
</div>

<div class="abs tile" style="left:71px;background:var(--purple)">
  <svg width="28" height="18" viewBox="0 0 28 18"><circle cx="8" cy="5" r="3" fill="#fff"/><circle cx="20" cy="5" r="3" fill="#fff"/><circle cx="14" cy="4" r="3.5" fill="#fff"/><path d="M2 16c0-5 12-5 12 0zM14 16c0-5 12-5 12 0zM7 17c0-6 14-6 14 0z" fill="#fff"/></svg>Consulting</div>
<div class="abs tile" style="left:217px;background:var(--sky)">
  <svg width="20" height="20" viewBox="0 0 20 20"><circle cx="10" cy="10" r="6" fill="none" stroke="#fff" stroke-width="3" stroke-dasharray="3 2"/><circle cx="10" cy="10" r="3" fill="none" stroke="#fff" stroke-width="1.5"/></svg>Engineering</div>
<div class="abs tile" style="left:362px;background:var(--rose)">
  <svg width="16" height="20" viewBox="0 0 16 20"><circle cx="6" cy="3" r="2" fill="#fff"/><path d="M5 6h3v8h5v3H5z" fill="#fff"/></svg>Construction</div>
<div class="abs tile" style="left:507px;background:var(--mint)">
  <svg width="20" height="20" viewBox="0 0 20 20"><circle cx="10" cy="10" r="6.5" fill="none" stroke="#fff" stroke-width="3" stroke-dasharray="2.5 1.5"/></svg>Operations</div>
<div class="abs tile" style="left:652px;background:var(--steel)">
  <svg width="20" height="20" viewBox="0 0 20 20"><path d="M4 4l12 12M16 4L4 16" stroke="#fff" stroke-width="2.5"/></svg>Maintenance</div>

<div class="abs sec-head" style="left:72px;top:562px"><span class="sec-mark"></span>About Us</div>
<div class="abs rule" style="left:92px;top:583px;width:273px"></div>
<div class="abs rule-red" style="left:92px;top:583px;width:62px"></div>
<div class="abs" style="left:71px;top:603px;width:90px;height:105px;background:linear-gradient(#e9eef2,#b8c7d6)" role="img" aria-label="Photo of smiling business team"></div>
<p class="abs about-text">quelbrant is a joint venture between varlenta construction, orvik worldwide and tessam engineering &amp; management company founded in bangkok, thailand in 2003 and brenn electrical construction company founded in san francisco, california in 2001. developed by former kestrel, holmfeld and dale harrow and pike employees with over 30 years experience in engineering and construction of systems around the globe.</p>

<div class="abs sec-head" style="left:390px;top:562px"><span class="sec-mark"></span>Hot News</div>
<div class="abs rule" style="left:410px;top:583px;width:367px"></div>
<div class="abs rule-red" style="left:410px;top:583px;width:48px"></div>
<div class="abs" style="left:745px;top:565px;width:14px;height:14px;background:var(--red)"><svg width="14" height="14"><path d="M8.5 4L5.5 7l3 3" fill="none" stroke="#fff" stroke-width="1.6"/></svg></div>
<div class="abs" style="left:763px;top:565px;width:14px;height:14px;background:#aaa"><svg width="14" height="14"><path d="M5.5 4l3 3-3 3" fill="none" stroke="#fff" stroke-width="1.6"/></svg></div>
<div class="abs" style="left:391px;top:594px;width:189px;height:125px;background:linear-gradient(120deg,#eef1f4,#aab3bf)" role="img" aria-label="Photo of a businessman in a meeting"></div>
<div class="abs news-meta">October 15, 2013 &nbsp;&nbsp; ● 0 &nbsp; ◉ 288 &nbsp; ▮ Kids</div>
<div class="abs" style="left:593px;top:620px;width:14px;height:13px;background:var(--red)"><svg width="14" height="13"><path d="M4 9l5-5 1.5 1.5-5 5H4z" fill="#fff"/></svg></div>
<div class="abs news-title">Lorem ipsum dolor sit amit the contantry sit</div>
<div class="abs stars" style="left:593px;top:651px">★★★★☆</div>
<p class="abs news-text">Lorem ipsum dolor sit amet, consectetur adipiscing elit. Tollenda est atque extrahenda</p>
<div class="abs btn-red" style="left:593px;top:699px">Read More ›</div>

<div class="abs sec-head" style="left:72px;top:753px"><span class="sec-mark"></span>Latest Events</div>
<div class="abs rule" style="left:92px;top:774px;width:685px"></div>
<div class="abs rule-red" style="left:92px;top:774px;width:72px"></div>

<article class="abs card" style="left:71px"><div class="card-img" role="img" aria-label="Photo of a hand touching a network diagram" style="background:linear-gradient(#c8c8c8,#555)"></div><h3>Lorem ipsum dolor sit amit</h3><p>Posted on <span>7 April, 2013</span> By <span>lorem</span></p><div class="rate"><b>★★</b>★★★</div></article>
<article class="abs card" style="left:254px"><div class="card-img" role="img" aria-label="Photo of a social network of people icons" style="background:linear-gradient(#9aa0b2,#5c6277)"></div><h3>How to budget for living abroad</h3><p>Posted on <span>7 April, 2013</span> By <span>contantry</span></p><div class="rate"><b>★★</b>★★★</div></article>
<article class="abs card" style="left:438px"><div class="card-img" role="img" aria-label="Photo of a tablet showing a chart" style="background:linear-gradient(#e8eef2,#9aa6ae)"></div><h3>Contantry popilar</h3><p>Posted on <span>7 April, 2013</span> By <span>ipsum sit</span></p><div class="rate"><b>★★</b>★★★</div></article>
<article class="abs card" style="left:622px"><div class="card-img" role="img" aria-label="Photo of hands holding a globe" style="background:radial-gradient(circle at 50% 50%,#4a6f9a,#d9c5b3 70%)"></div><h3>How to budget for living abroad</h3><p>Posted on <span>7 April, 2013</span> By <span>popilar lor</span></p><div class="rate"><b>★★</b>★★★</div></article>

<footer class="abs footer">
  <div class="abs foot-mark"></div>
  <div class="abs" style="left:71px;top:36px;width:260px;height:1px;background:#888"></div>
  <div class="abs" style="left:519px;top:36px;width:257px;height:1px;background:#888"></div>
  <div class="abs foot-title">QUELBRANT INTERNATIONAL</div>
  <div class="abs branch" style="left:72px"><h4>Main Office Bangkok Branch</h4>41 lorvane rd, tessit, marlow,<br>bangkok 10990
    <dl><dt>Phone</dt><dd>+00 2 5550 1010</dd><dt>Fax</dt><dd>+00 2 5550 1011</dd><dt>e-mail</dt><dd>bangkok@norlicetta-example.com</dd></dl></div>
  <div class="abs branch" style="left:252px"><h4>Sukumvit Branch</h4>212/7 oransay house, velmor rd,<br>&nbsp;
    <dl><dt>Phone</dt><dd>+00 3 5550 2020</dd><dt>Fax</dt><dd>+00 3 5550 2021</dd><dt>e-mail</dt><dd>office@norlicetta-example.com</dd></dl></div>
  <div class="abs branch" style="left:432px"><h4>Pattaya Branch</h4>18/2 m.4 kestamit rd, palu-ree,<br>sarnwong, chonburi 20990
    <dl><dt>Phone</dt><dd>+00 4 5550 3030</dd><dt>Fax</dt><dd>+00 4 5550 3031</dd><dt>e-mail</dt><dd>office@norlicetta-example.com</dd></dl></div>
  <div class="abs contact" style="left:667px;top:53px"><h4>CONTACT US</h4>
    <div class="field">Enter your Name</div><div class="field">Enter your email id</div><div class="btn-contact">Contact Us</div></div>
</footer>
<div class="abs bottom">
  <div class="abs" style="left:72px;top:16px">Copyright © 2014 - quelbrant - All Right Reserved</div>
  <div class="abs social" aria-label="Social links"><span></span><span></span><span></span><span></span><span></span><span></span></div>
</div>

</body>
</html>
```